Freelance Translator in Need of a Business Card

I am a freelance Japanese to English translator. I work in the video game localization industry and do literary translation in my spare time. I would like to have both the English word 'Translator' and the Japanese '翻訳者' in the job title. The final design should evoke trust, openness, and reliability.

Target Market(s)

Video game localization companies
Japanese comic book artists

Industry/Entity Type

Business

Contact Information for Business Card

Daniel Forsvik, Translator
dan.forsvik@quellmail.net
torvenwords.com
twitter: @torven_wd

Colors

Designer to choose colors to be used in the design.

```html
<!DOCTYPE html>
<html lang="en">
<head>
<meta charset="utf-8">
<title>Torven Words – Business Card</title>
<link rel="stylesheet" href="https://fonts.googleapis.com/css2?family=Playfair+Display:wght@400;700&family=Noto+Serif+JP:wght@400&display=swap">
<style>
  :root {
    --backdrop: #e9e6e1;
    --card-white: #ffffff;
    --card-black: #1a1a1a;
    --band-dark: #262424;
    --band-light: #f1f1f1;
    --ink-dark: #151515;
    --ink-light: #f4f4f4;
    --ink-muted: #555555;
    --serif: 'Playfair Display', 'Noto Serif JP', Georgia, serif;
  }
  * { margin: 0; padding: 0; box-sizing: border-box; }
  html, body { width: 1200px; height: 892px; overflow: hidden; }
  body {
    background: var(--backdrop);
    font-family: var(--serif);
    position: relative;
  }
  .card {
    position: absolute;
    top: 286px;
    width: 560px;
    height: 320px;
    box-shadow: 0 6px 18px rgba(0,0,0,0.18);
    overflow: hidden;
  }
  /* Front */
  .card--front { left: 27px; background: var(--card-white); }
  .front__title {
    position: absolute; left: 40px; top: 42px;
    font-size: 46px; font-weight: 700; color: var(--ink-dark);
    letter-spacing: 0.5px;
  }
  .front__band {
    position: absolute; left: 150px; right: 0; top: 128px; height: 108px;
    background: var(--band-dark);
  }
  .front__person {
    position: absolute; left: 22px; top: 26px; color: var(--ink-light);
  }
  .front__name { font-size: 27px; font-weight: 400; line-height: 1.1; }
  .front__role { font-size: 14px; margin-top: 4px; font-family: 'Playfair Display', 'Noto Serif JP', serif; }
  .front__role .jp { font-family: 'Noto Serif JP', serif; }
  .front__contacts {
    position: absolute; left: 232px; top: 34px;
    list-style: none; color: var(--ink-light); font-size: 12.5px;
  }
  .front__contacts li { display: flex; align-items: center; gap: 9px; height: 21px; }
  .front__contacts svg { width: 14px; height: 14px; flex: none; }
  .front__social {
    position: absolute; left: 150px; top: 262px;
    font-size: 14px; color: var(--ink-muted);
  }
  /* Back */
  .card--back { left: 613px; background: var(--card-black); }
  .back__band {
    position: absolute; left: 0; right: 0; top: 92px; height: 136px;
    background: var(--band-light);
    display: flex; align-items: center; justify-content: center;
  }
  .back__title {
    font-size: 42px; font-weight: 700; color: var(--ink-dark);
    letter-spacing: 1px; text-transform: uppercase;
  }
</style>
</head>
<body>
  <section class="card card--front" aria-label="Business card front">
    <h1 class="front__title">Torven Words</h1>
    <div class="front__band">
      <div class="front__person">
        <p class="front__name">Daniel Forsvik</p>
        <p class="front__role">Translator <span class="jp" lang="ja">翻訳者</span></p>
      </div>
      <ul class="front__contacts">
        <li>
          <svg viewBox="0 0 14 14" aria-hidden="true">
            <rect x="1" y="3" width="12" height="8" fill="#f4f4f4"/>
            <path d="M1 3 L7 8 L13 3" fill="none" stroke="#262424" stroke-width="1.2"/>
          </svg>
          dan.forsvik@quellmail.net
        </li>
        <li>
          <svg viewBox="0 0 14 14" aria-hidden="true" fill="none" stroke="#f4f4f4" stroke-width="1.1">
            <circle cx="7" cy="7" r="5.8"/>
            <ellipse cx="7" cy="7" rx="2.6" ry="5.8"/>
            <line x1="1.2" y1="7" x2="12.8" y2="7"/>
            <line x1="2.2" y1="4" x2="11.8" y2="4"/>
            <line x1="2.2" y1="10" x2="11.8" y2="10"/>
          </svg>
          www.torvenwords.com
        </li>
      </ul>
    </div>
    <p class="front__social">twitter: @torven_wd</p>
  </section>

  <section class="card card--back" aria-label="Business card back">
    <div class="back__band">
      <p class="back__title">Torven Words</p>
    </div>
  </section>
</body>
</html>
```